Telecommunications Company needs a business card design

We are looking for a sleek, professional and modern business card design based off our new logo. Will look at both light and dark options. On some designs please provide a small space for a QR code

Target Market(s)

B2B clients in Australia

Contact Information for Business Card

Name, Position, Brisbane (head) office, Phone number, email address, QR code (link to our website qlinetelecom.com.au

Colors
0054AA
0677BA
7BADD7
CADEEF
E8F1F8
0094D4
00A9DD
6FCCEA
C7EBF8
E9F6FB
00AB8E
00BBA5
67D7C9
C6EFE9
E9F9F6

```html
<!DOCTYPE html>
<html lang="en">
<head>
<meta charset="utf-8">
<title>Qline Telecom – Business Card</title>
<link href="https://fonts.googleapis.com/css2?family=Montserrat:wght@400;500;700&display=swap" rel="stylesheet">
<style>
  :root {
    --bg: #1c1c1c;
    --card: #252525;
    --card-edge: #2c2c2c;
    --blue: #0677BA;
    --blue-strong: #0054AA;
    --teal: #00AB8E;
    --text: #f2f2f2;
    --muted: #b9bec3;
  }
  * { box-sizing: border-box; margin: 0; padding: 0; }
  html, body {
    width: 1200px; height: 900px; overflow: hidden;
    background: radial-gradient(circle at 50% 45%, #262626 0%, var(--bg) 70%);
    font-family: "Montserrat", sans-serif;
  }
  .stage {
    width: 1200px; height: 900px;
    display: flex; flex-direction: column; align-items: center; justify-content: center;
    gap: 40px;
  }
  .card {
    position: relative;
    width: 620px; height: 354px;
    background: linear-gradient(135deg, var(--card) 0%, var(--card-edge) 100%);
    border-bottom: 6px solid var(--blue);
    box-shadow: 0 18px 40px rgba(0,0,0,.55);
  }
  .card--front { display: flex; align-items: center; justify-content: center; }
  .brand { display: flex; align-items: center; gap: 14px; }
  .brand__dot { width: 22px; height: 22px; border-radius: 50%; background: var(--teal); }
  .brand__name {
    font-weight: 700; font-size: 38px; color: var(--blue);
    letter-spacing: 1px; text-transform: uppercase;
  }
  .card--back {
    display: flex; align-items: center; padding-left: 96px; padding-top: 10px;
  }
  .identity { text-align: right; width: 230px; }
  .identity__name {
    font-weight: 700; font-size: 24px; color: var(--blue);
    text-transform: uppercase; letter-spacing: .3px; text-align: left;
  }
  .identity__role, .identity__office {
    font-size: 16px; color: var(--text); line-height: 1.3;
  }
  .divider { width: 3px; height: 66px; background: var(--teal); margin: 0 28px 0 28px; }
  .contact { list-style: none; display: flex; flex-direction: column; gap: 4px; padding-top: 14px; }
  .contact__item {
    display: flex; align-items: center; gap: 10px;
    font-size: 17px; color: var(--text);
  }
  .contact__icon { width: 15px; height: 15px; flex: none; }
</style>
</head>
<body>
  <main class="stage">
    <section class="card card--front" aria-label="Card front">
      <div class="brand">
        <span class="brand__dot"></span>
        <span class="brand__name">Qline Telecom</span>
      </div>
    </section>

    <section class="card card--back" aria-label="Card back">
      <div class="identity">
        <p class="identity__name">Daniel Hart</p>
        <p class="identity__role">Director</p>
        <p class="identity__office">Brisbane (head) office</p>
      </div>
      <div class="divider"></div>
      <ul class="contact">
        <li class="contact__item">
          <svg class="contact__icon" viewBox="0 0 24 24" fill="none" stroke="#0677BA" stroke-width="2" stroke-linecap="round" stroke-linejoin="round"><path d="M6 3h3l2 5-2.5 1.5a11 11 0 0 0 6 6L16 13l5 2v3a2 2 0 0 1-2 2A16 16 0 0 1 4 5a2 2 0 0 1 2-2z"/></svg>
          (07) 5550 1234
        </li>
        <li class="contact__item">
          <svg class="contact__icon" viewBox="0 0 24 24" fill="none" stroke="#0677BA" stroke-width="2" stroke-linejoin="round"><rect x="3" y="5" width="18" height="14" rx="1"/><path d="M3 6l9 7 9-7"/></svg>
          qlinetelecom.com.au
        </li>
        <li class="contact__item">
          <svg class="contact__icon" viewBox="0 0 24 24" fill="none" stroke="#0677BA" stroke-width="2"><circle cx="12" cy="12" r="9"/><ellipse cx="12" cy="12" rx="4" ry="9"/><path d="M3 12h18M5 7h14M5 17h14"/></svg>
          qlinetelecom.com.au
        </li>
      </ul>
    </section>
  </main>
</body>
</html>
```